A parent Company needs a website as a leading diversified business in industrial Conglomerates in Af

Velkor Group is a private (Holding) limited liability company incorporated under the Companies Code, 1963 (Act 179) in November, 2013 to following the speedy growth in numbers of its current subsidiaries which has been founded several years ago with an emerging force to become one of the largest and a leading diversified business in industrial Conglomerates in Africa.
The Group which is 100% wholly owned indigenous Ghanaian Company focuses on provision of local, value-added products and services that meet the needs of the African population. The Group is headquartered in Accra, Ghana with interests across a range of sectors in Africa.
We are currently into Food & Beverage, Real Estate Development, Transportation, Health Care, Consumer Products Distribution, Agro Processing, Manufacturing, ICT, Exports & Import, and still counting.
In the next 3 years, we shall announce our ambitions to enter Ghana's largest Oil and Gas industry, playing a strategic role in the petroleum sector with strategic alliances, and help build Ghana's biggest and most important Energy sector in the country.
Inspired by billionaires Tom Prewitt, Harlan Voskel, and Emeka Ofodile, Velkor Group (Velkor Foundation) is committed to making a name for itself on the philanthropic circuit and has given away privately and still given to the cause to the needy in the society and some specific social causes in Ghana.
The company is managed by a 5 member board and a 2 member advisory experts who are non-board members.
The company has a vision, mission and it is guided by its core values.
We would like to see a designs that is very professional and looks corporate and can attract investors and partners. It must communicate financial safety and growth and must reflect our logo colors.

```html
<!DOCTYPE html>
<html lang="en">
<head>
<meta charset="utf-8">
<title>Velkor Group</title>
<link href="https://fonts.googleapis.com/css2?family=Open+Sans:wght@300;400;600&family=Ubuntu:wght@400;500&display=swap" rel="stylesheet">
<style>
:root{
  --blue:#1a6fb8;
  --cyan:#1ea3de;
  --red:#b8000f;
  --nav:#4d4d4f;
  --panel:#3c3c41;
  --ink:#3a3a3a;
  --muted:#6b6b6b;
  --box:#efefef;
  --line:#d8d8d8;
  --foot:#2f2f31;
  --foot-text:#c9c9c9;
}
*{margin:0;padding:0;box-sizing:border-box}
html,body{width:1056px;height:1200px;overflow:hidden;background:#fff}
body{position:relative;font-family:"Open Sans",Arial,sans-serif;color:var(--ink)}
.abs{position:absolute}

/* header */
.brand{left:97px;top:26px;display:flex;align-items:center;gap:12px}
.brand-mark{width:54px;height:54px;border-radius:50%;background:var(--blue)}
.brand-name{font-size:19px;font-weight:400;color:#333;letter-spacing:.3px}
.social-top{left:655px;top:44px;display:flex;gap:17px}
.social-top span{width:16px;height:16px;border-radius:50%;background:#6a6a6a}
.top-sep{left:786px;top:44px;width:1px;height:17px;background:#ccc}
.top-links{left:800px;top:45px;display:flex;gap:15px;font-size:10px;color:#8a8a8a}

/* nav */
.nav{left:0;top:100px;width:1056px;height:42px;background:var(--nav)}
.nav-shadow{left:97px;top:142px;width:862px;height:20px;background:radial-gradient(ellipse at top,rgba(0,0,0,.18),rgba(0,0,0,0) 70%)}
.nav-home{left:97px;top:100px;width:54px;height:42px;background:var(--blue);display:flex;align-items:center;justify-content:center}
.nav-items{left:167px;top:100px;height:42px;display:flex;align-items:center;gap:26px;font-size:11.5px;color:#fff}
.nav-search{left:906px;top:100px;width:53px;height:42px;background:var(--cyan);display:flex;align-items:center;justify-content:center}

/* hero */
.hero-frame{left:90px;top:171px;width:876px;height:336px;border:1px solid #d5d5d5;border-radius:4px;box-shadow:0 1px 3px rgba(0,0,0,.08)}
.hero-photo{left:97px;top:177px;width:640px;height:323px;background:linear-gradient(120deg,#3c3f48 0%,#8d8a86 35%,#e6e3df 60%,#f7f7f7 100%)}
.hero-caption{left:97px;top:425px;width:640px;height:75px;background:linear-gradient(to top,rgba(0,0,0,.75),rgba(0,0,0,0))}
.hero-title{left:105px;top:432px;font-family:"Ubuntu",sans-serif;font-weight:500;font-size:22px;color:#fff}
.hero-sub{left:106px;top:463px;width:400px;font-size:10.5px;line-height:15px;color:#fff}
.hero-panel{left:739px;top:177px;width:220px;height:323px;background:var(--panel);color:#fff}
.hero-panel h1{position:absolute;left:17px;top:18px;font-weight:400;font-size:26px;letter-spacing:-.2px}
.hero-panel p{position:absolute;left:19px;top:62px;width:190px;font-size:11.3px;line-height:17.6px}
.btn-red{position:absolute;left:19px;top:217px;width:91px;height:29px;background:var(--red);font-size:11px;display:flex;align-items:center;padding-left:8px;gap:8px}
.arrows{position:absolute;left:21px;top:291px;display:flex;gap:6px}
.arrows span{width:20px;height:19px;background:var(--red);display:flex;align-items:center;justify-content:center}

/* sectors */
.sectors{left:106px;top:546px;width:846px;height:200px;background:var(--box);border:1px solid var(--line);border-radius:4px;display:flex}
.sector{position:relative;flex:1;border-right:1px solid #dcdcdc}
.sector:last-child{border-right:0}
.sector-head{height:57px;border-bottom:1px dashed #bdbdbd;display:flex;align-items:center;justify-content:center;gap:10px;color:var(--blue);font-size:22px;letter-spacing:-.3px}
.sector p{position:absolute;left:28px;top:70px;width:225px;font-size:11.3px;line-height:15px;color:var(--muted)}
.sector-btn{position:absolute;top:153px;height:31px;width:236px;background:#3a3a3b;border:1px solid #222;border-radius:2px;color:#fff;font-size:11.3px;display:flex;align-items:center;justify-content:space-between;padding:0 8px}

/* welcome */
.welcome-title{left:113px;top:792px;font-size:23px;font-weight:300;color:#444;letter-spacing:-.4px}
.welcome-title .accent{color:var(--red);font-weight:400}
.welcome-title .strong{color:#444;font-weight:400}
.welcome-text{left:113px;top:835px;width:556px;font-size:11.3px;line-height:15.8px;color:#444}
.welcome-link{left:113px;top:913px;font-size:11px;color:var(--blue);text-decoration:underline}
.find-title{left:723px;top:792px;font-family:"Ubuntu",sans-serif;font-size:16px;color:#444}
.find-bars{left:724px;top:819px;display:flex;gap:3px}
.find-bars span{height:4px;background:#7a7a7a}
.find-map{left:723px;top:832px;width:188px;height:105px;background:radial-gradient(ellipse at 35% 50%,#d9d9d9,#f3f3f3 75%,#fff)}

/* footer */
.footer{left:0;top:984px;width:1056px;height:216px;background:var(--foot);border-top:5px solid #6f6f71}
.foot-h{font-family:"Ubuntu",sans-serif;font-size:14px;color:#fff}
.foot-list{list-style:none;font-size:10.5px;line-height:17.6px;color:var(--foot-text)}
.news-input{left:726px;top:1037px;width:224px;height:31px;background:#fff;border:1px solid #ccc;font-size:9px;font-style:italic;color:#999;display:flex;align-items:center;padding-left:12px}
.foot-social{left:726px;top:1084px;display:flex;gap:9px}
.foot-social span{width:20px;height:20px;border-radius:50%;background:#5e6a78}
.foot-rule{left:107px;top:1156px;width:820px;height:1px;background:#4c4c4e}
.foot-bottom{left:0;top:1170px;width:1056px;text-align:center;font-size:10.5px;color:#8d8d8d}
.foot-bottom i{font-style:normal;margin:0 8px}
</style>
</head>
<body>

<header>
  <div class="abs brand"><span class="brand-mark"></span><span class="brand-name">VELKOR GROUP</span></div>
  <div class="abs social-top" aria-label="Social links"><span></span><span></span><span></span><span></span></div>
  <div class="abs top-sep"></div>
  <nav class="abs top-links"><span>About Us</span><span>Support</span><span>Contact Us</span></nav>
</header>

<div class="abs nav"></div>
<div class="abs nav-shadow"></div>
<div class="abs nav-home">
  <svg width="24" height="22" viewBox="0 0 24 22"><path d="M12 2 1 11h3v9h6v-6h4v6h6v-9h3z" fill="#fff"/></svg>
</div>
<nav class="abs nav-items">
  <span>Food &amp; Beverage</span><span>Transportation</span><span>Health Care</span><span>Consumer Products Distribution</span><span>Agro Processing</span><span>Exports &amp; Import</span>
</nav>
<div class="abs nav-search">
  <svg width="18" height="18" viewBox="0 0 18 18"><circle cx="7.5" cy="7.5" r="5.5" fill="none" stroke="#fff" stroke-width="2.4"/><path d="M11.5 11.5 16 16" stroke="#fff" stroke-width="2.6" stroke-linecap="round"/></svg>
</div>

<section>
  <div class="abs hero-frame"></div>
  <div class="abs hero-photo" role="img" aria-label="Photo of three business colleagues reviewing a presentation in an office"></div>
  <div class="abs hero-caption"></div>
  <div class="abs hero-title">Life’s Better When We’re Connected</div>
  <div class="abs hero-sub">Lorem Ipsum is simply dummy text of the printing and typesetting industry. Lorem Ipsum has been the industry's standard dummy text ever since</div>
  <div class="abs hero-panel">
    <h1>VELKOR GROUP</h1>
    <p>Lorem Ipsum is simply dummy text of the printing and typesetting industry. Lorem Ipsum has been the industry's standard dummy text ever since the 1500s, when an unknown printer took a galley of type and scrambled it to make a type specimen book.</p>
    <div class="btn-red">Read More <svg width="11" height="11" viewBox="0 0 11 11"><path d="M4 0h3v4h4v3H7v4H4V7H0V4h4z" fill="#fff"/></svg></div>
    <div class="arrows">
      <span><svg width="8" height="10" viewBox="0 0 8 10"><path d="M6 1 2 5l4 4" fill="none" stroke="#fff" stroke-width="2"/></svg></span>
      <span><svg width="8" height="10" viewBox="0 0 8 10"><path d="M2 1l4 4-4 4" fill="none" stroke="#fff" stroke-width="2"/></svg></span>
    </div>
  </div>
</section>

<section class="abs sectors">
  <div class="sector">
    <div class="sector-head">
      <svg width="22" height="30" viewBox="0 0 22 30"><path d="M2 1v9q0 3 3 3v16h2V13q3 0 3-3V1H8v8H7V1H5v8H4V1z" fill="#444"/><path d="M15 1q5 2 5 12h-3v16h-2z" fill="#444"/></svg>
      <span>Food &amp; Beverages</span>
    </div>
    <p>Lorem Ipsum is simply dummy text of the printing and typesetting industry. Lorem Ipsum has been the industry's standard dummy text ever since the</p>
    <div class="sector-btn" style="left:22px">Read more about Food &amp; Beverages
      <svg width="20" height="20" viewBox="0 0 20 20"><circle cx="10" cy="10" r="10" fill="var(--cyan)"/><path d="M5 10h8M10 6l4 4-4 4" fill="none" stroke="#fff" stroke-width="2.4"/></svg></div>
  </div>
  <div class="sector">
    <div class="sector-head">
      <svg width="34" height="24" viewBox="0 0 34 24"><path d="M1 2h19v15H1zM21 7h7l5 6v4H21z" fill="#444"/><circle cx="7" cy="20" r="3.2" fill="#444" stroke="#efefef" stroke-width="1.5"/><circle cx="27" cy="20" r="3.2" fill="#444" stroke="#efefef" stroke-width="1.5"/></svg>
      <span>Transportation</span>
    </div>
    <p>Lorem Ipsum is simply dummy text of the printing and typesetting industry. Lorem Ipsum has been the industry's standard dummy text ever since the</p>
    <div class="sector-btn" style="left:27px">Read more about Transportation
      <svg width="20" height="20" viewBox="0 0 20 20"><circle cx="10" cy="10" r="10" fill="var(--cyan)"/><path d="M5 10h8M10 6l4 4-4 4" fill="none" stroke="#fff" stroke-width="2.4"/></svg></div>
  </div>
  <div class="sector">
    <div class="sector-head">
      <svg width="30" height="30" viewBox="0 0 30 30"><rect x="1.5" y="1.5" width="27" height="27" fill="none" stroke="#444" stroke-width="2.4"/><path d="M4 16h6l2-6 3 11 3-9 2 4h6" fill="none" stroke="#444" stroke-width="2"/></svg>
      <span>Health &amp; Care</span>
    </div>
    <p>Lorem Ipsum is simply dummy text of the printing and typesetting industry. Lorem Ipsum has been the industry's standard dummy text ever since the</p>
    <div class="sector-btn" style="left:18px">Read more about Health &amp; Care
      <svg width="20" height="20" viewBox="0 0 20 20"><circle cx="10" cy="10" r="10" fill="var(--cyan)"/><path d="M5 10h8M10 6l4 4-4 4" fill="none" stroke="#fff" stroke-width="2.4"/></svg></div>
  </div>
</section>

<section>
  <h2 class="abs welcome-title">Welcome to <span class="accent">VELKOR</span> <span class="strong">Group</span> Tenacity, Integrity &amp; Passion</h2>
  <p class="abs welcome-text">Velkor Group is a private (Holding) limited liability company incorporated under the Companies Code, 1963 (Act 179) in November, 2013 to following the speedy growth in numbers of its current subsidiaries which has been founded several years ago with an emerging force to become one of the largest and a leading diversified business in industrial Conglomerates in Africa.</p>
  <span class="abs welcome-link">Read More</span>
  <h3 class="abs find-title">Find Us</h3>
  <div class="abs find-bars"><span style="width:50px"></span><span style="width:20px"></span><span style="width:28px"></span><span style="width:66px;background:#a5a5a5"></span></div>
  <div class="abs find-map" role="img" aria-label="World map highlighting the Americas and West Africa where the group operates"></div>
</section>

<footer class="abs footer"></footer>
<div class="abs foot-h" style="left:107px;top:1002px">Links</div>
<ul class="abs foot-list" style="left:107px;top:1024px">
  <li>Home</li><li>Food &amp; Beverage</li><li>Transportation</li><li>Health Care</li><li>Consumer Products Distribution</li><li>Agro Processing</li><li>Import &amp; Export</li>
</ul>
<div class="abs foot-h" style="left:331px;top:1003px">About Us</div>
<ul class="abs foot-list" style="left:328px;top:1037px">
  <li>The Velkor Group</li><li>Lorem Lipsum</li><li style="text-decoration:underline">Read More</li>
</ul>
<div class="abs foot-h" style="left:498px;top:1003px">Connect with us</div>
<ul class="abs foot-list" style="left:500px;top:1036px;line-height:16px">
  <li>info@velkorgroup.com</li><li>+233-0-302-4418</li>
</ul>
<div class="abs foot-h" style="left:727px;top:1013px">Sign up for newsletter</div>
<div class="abs news-input">Enter Your Email Address</div>
<div class="abs foot-social" aria-label="Social links"><span></span><span></span><span></span><span></span></div>
<div class="abs foot-rule"></div>
<div class="abs foot-bottom">2014, Velkor Group. Privacy Policy<i>|</i>Terms of Service<i>|</i>Help<i>|</i>Contact</div>

</body>
</html>
```